I would like a business card to match my truck wrap and logo. I would like the font to match my existing business card please.

Industry/Entity Type

Painter

Contact Information for Business Card

Rodrigo Fenwar 801-437-2190 Fenwarcoatings.utah@brelmox.com
SERVICES - Custom Paint & Stain, Interior & Exterior, Epoxy Coatings / Garage Floors, Cabinet Refinishing, Log Staining and Refinishing.

Requirements
Nice to have
• I would like to have the white and grey line like the bottom of my vehicle wrap, Light Grey to match my truck also.

```html
<!DOCTYPE html>
<html lang="en">
<head>
<meta charset="utf-8">
<title>Fenwar Coatings – Business Card</title>
<link rel="stylesheet" href="https://fonts.googleapis.com/css2?family=Arimo:wght@400;700&display=swap">
<style>
  :root {
    --backdrop: #1f1f1f;
    --card-front: #f2f2f2;
    --card-back: #ffffff;
    --brand-blue: #12a6e6;
    --deep-blue: #0d6bb0;
    --band-grey: #b0b7c4;
    --text-dark: #3a3a3a;
  }
  html, body {
    margin: 0;
    padding: 0;
    width: 1093px;
    height: 1200px;
    overflow: hidden;
    background: var(--backdrop);
    font-family: "Arimo", Arial, sans-serif;
  }
  .card {
    position: absolute;
    left: 264px;
    width: 580px;
    height: 357px;
    overflow: hidden;
    box-shadow: 0 3px 8px rgba(0,0,0,0.6);
  }
  .card--front { top: 226px; background: var(--card-front); }
  .card--back  { top: 620px; background: var(--card-back); }

  .brand {
    position: absolute;
    left: 40px;
    top: 52px;
    display: flex;
    align-items: center;
    gap: 18px;
  }
  .brand__mark {
    width: 62px;
    height: 62px;
    background: var(--brand-blue);
    border-radius: 6px;
  }
  .brand__name {
    color: var(--brand-blue);
    font-weight: 700;
    font-size: 40px;
    line-height: 1;
    letter-spacing: 1px;
  }
  .brand__name span { display: block; font-size: 17px; letter-spacing: 11px; margin-top: 8px; }

  .contact { position: absolute; left: 176px; top: 188px; }
  .contact__name {
    margin: 0 0 20px;
    color: var(--deep-blue);
    font-weight: 700;
    font-size: 22px;
    text-transform: uppercase;
    letter-spacing: 0.3px;
  }
  .contact__line {
    display: flex;
    align-items: center;
    gap: 7px;
    color: var(--text-dark);
    font-size: 17px;
    line-height: 21px;
  }
  .contact__line svg { width: 16px; height: 16px; }

  .services {
    position: absolute;
    left: 182px;
    top: 145px;
    margin: 0;
    padding: 0;
    list-style: none;
  }
  .services li {
    display: flex;
    align-items: center;
    gap: 10px;
    color: var(--text-dark);
    font-size: 17.5px;
    height: 28.5px;
  }
  .services li::before {
    content: "";
    width: 11px;
    height: 11px;
    background: linear-gradient(135deg, var(--brand-blue), var(--deep-blue));
    transform: rotate(45deg);
    margin: 0 2px;
  }

  .band { position: absolute; left: 0; bottom: 0; width: 580px; height: 70px; }
</style>
</head>
<body>

<section class="card card--front">
  <div class="brand">
    <div class="brand__mark"></div>
    <div class="brand__name">FENWAR<span>COATINGS</span></div>
  </div>
  <div class="contact">
    <h1 class="contact__name">Rodrigo Fenwar</h1>
    <div class="contact__line">
      <svg viewBox="0 0 16 16" aria-hidden="true"><path d="M3 1l3 3-2 2c1 2 3 4 5 5l2-2 3 3-2 3C6 15 1 10 1 3z" fill="var(--deep-blue)"/></svg>
      801-437-2190
    </div>
    <div class="contact__line">
      <svg viewBox="0 0 16 16" aria-hidden="true"><rect x="1" y="3" width="14" height="10" fill="var(--deep-blue)"/><path d="M1 3l7 6 7-6" stroke="#fff" stroke-width="1.2" fill="none"/></svg>
      Fenwarcoatings.utah@brelmox.com
    </div>
  </div>
  <svg class="band" viewBox="0 287 580 70" aria-hidden="true">
    <polyline points="0,300 173,300 204,333 580,333" fill="none" stroke="var(--band-grey)" stroke-width="4"/>
    <polygon points="0,309 163,309 194,343 580,343 580,357 0,357" fill="var(--band-grey)"/>
  </svg>
</section>

<section class="card card--back">
  <div class="brand">
    <div class="brand__mark"></div>
    <div class="brand__name">FENWAR<span>COATINGS</span></div>
  </div>
  <ul class="services">
    <li>Custom Paint &amp; Stain</li>
    <li>Interior &amp; Exterior</li>
    <li>Epoxy Coatings/ Garage Floors</li>
    <li>Cabinet Refinishing</li>
    <li>Log Staining and Refinishing.</li>
  </ul>
  <svg class="band" viewBox="0 287 580 70" aria-hidden="true">
    <polyline points="0,300 173,300 204,333 580,333" fill="none" stroke="var(--band-grey)" stroke-width="4"/>
    <polygon points="0,309 163,309 194,343 580,343 580,357 0,357" fill="var(--band-grey)"/>
  </svg>
</section>

</body>
</html>
```